Business Card Design

We like to use greens as you will see in our logo (but not TOO much green). We are a Dental Clinic in a somewhat eccentric community. We do not like the dated sharp designs which we see many dentists use. We're looking for something bright and fresh while still maintaining the integrity of the profession. Elegance is not necessarily what we are going for... we need for the design to be "mature" but also up-lifting.

See our logo.
Updates

Project Deadline Extended
Reason: We have 5 designs which we like. But we'd like to see a few more before committing to a design.

Project Deadline Extended
Reason: We are awaiting revisions to this project. We are still welcoming designs while we wait to see if designers are able to provide to us the revisions we require in order to proceed with a selection.

Target Market(s)

Younger families - ages late 20's to early 40's

Industry/Entity Type

Business

Contact Information for Business Card

Corwel T. Banfry DDS 2730 W. Halvert Rd. Ste. 7 Royal Oak, MI 48391 (248)555-0174 FX (248)555-0189 info@BrightwellDentalCareMi.com BrigthwellDentalCareMi.com on the back of the card we need an appointment reminder (For____ Date___ Time____) with "If you are unable to keep your appointment, kindly give 48 hours notice" at the bottom. No use of teeth in the design. DOUBLE SIDED DESIGN

Requirements
Should not have
• The use of pictures of teeth

```html
<!DOCTYPE html>
<html lang="en">
<head>
<meta charset="utf-8">
<title>Brightwell Dental Care – Business Card</title>
<link rel="stylesheet" href="https://fonts.googleapis.com/css2?family=Cinzel:wght@500;600&family=Arimo:wght@400;700&family=PT+Sans:ital@1&display=swap">
<style>
  :root {
    --backdrop: #ecebe8;
    --card: #ffffff;
    --green-dark: #1f6b3a;
    --green-mid: #2f8a4a;
    --green-soft: #9fcf8a;
    --band: #555555;
    --band-text: #ffffff;
    --label: #555555;
    --rule: #777777;
    --box: #666666;
  }
  * { box-sizing: border-box; margin: 0; padding: 0; }
  html, body { width: 1200px; height: 1161px; overflow: hidden; }
  body { background: var(--backdrop); position: relative; font-family: "Arimo", Arial, sans-serif; }

  .card { position: absolute; background: var(--card); box-shadow: 0 4px 14px rgba(0,0,0,.18); overflow: hidden; }
  .card--front { left: 42px; top: 43px; width: 912px; height: 520px; }
  .card--back  { left: 235px; top: 602px; width: 911px; height: 518px; }

  /* front */
  .name-tag { position: absolute; left: 0; top: 52px; height: 74px; padding: 0 24px 0 22px; background: var(--green-dark);
    color: var(--band-text); font-weight: 700; font-size: 29px; display: flex; align-items: center; letter-spacing: .3px; }
  .name-tag .degree { font-size: 19px; margin-left: 7px; margin-top: 6px; }

  .brand { position: absolute; left: 480px; top: 92px; width: 400px; text-align: center;
    font-family: "Cinzel", Georgia, serif; font-weight: 600; color: var(--green-mid); }
  .brand__name { font-size: 58px; line-height: 1; letter-spacing: 1px; }
  .brand__sub { font-size: 36px; line-height: 1; margin-top: 18px; letter-spacing: 1.5px; }
  .brand__mark { display: block; width: 44px; height: 44px; border-radius: 50%; background: var(--green-mid); margin: 0 auto 18px; }

  .band { position: absolute; left: 0; top: 294px; width: 100%; height: 226px; background: var(--band); color: var(--band-text); }
  .band__dot { position: absolute; left: 104px; top: 22px; width: 52px; height: 52px; border-radius: 50%; background: var(--green-soft); }
  .address { position: absolute; left: 22px; top: 131px; font-size: 22px; line-height: 37px; font-style: normal; }
  .contacts { position: absolute; left: 482px; top: 28px; list-style: none; font-size: 22px; }
  .contacts li { display: flex; align-items: center; height: 46px; }
  .contacts li.web { font-size: 20px; }
  .contacts svg { width: 20px; height: 20px; margin-right: 10px; fill: var(--band-text); flex: none; }

  /* back */
  .watermark { position: absolute; left: 290px; top: 80px; width: 320px; height: 320px; border-radius: 50%; background: var(--green-soft); opacity: .35; }
  .appt-title { position: absolute; left: 0; top: 84px; width: 100%; text-align: center; font-family: "Cinzel", Georgia, serif;
    font-weight: 500; font-size: 35px; color: var(--green-dark); letter-spacing: .5px; }
  .field { position: absolute; left: 71px; font-size: 24px; color: var(--label); display: flex; align-items: flex-end; }
  .fill { display: inline-block; border-bottom: 2px dotted var(--rule); height: 4px; margin: 0 8px 7px; }
  .field--name { top: 150px; }
  .field--date { top: 214px; }
  .field--next { top: 280px; align-items: center; }
  .slot { display: inline-block; width: 164px; height: 36px; border: 2px solid var(--box); border-radius: 4px; margin-left: 13px; }
  .days { position: absolute; left: 68px; top: 362px; display: flex; align-items: center; font-size: 25px; font-weight: 700; color: var(--label); }
  .days span { margin-right: 12px; }
  .days .box { width: 56px; height: 34px; border: 2px solid var(--box); border-radius: 4px; margin-right: 22px; }
  .notice { position: absolute; left: 0; bottom: 42px; width: 100%; text-align: center; font-family: "PT Sans", "Trebuchet MS", sans-serif;
    font-style: italic; font-size: 24px; color: #333; }
</style>
</head>
<body>

<section class="card card--front" aria-label="Business card front">
  <div class="name-tag">CORWEL T. BANFRY,<span class="degree">DDS</span></div>

  <div class="brand">
    <span class="brand__mark"></span>
    <div class="brand__name">Brightwell</div>
    <div class="brand__sub">DENTAL CARE</div>
  </div>

  <div class="band">
    <span class="band__dot"></span>
    <address class="address">2730 W. Halvert Rd.<br>Ste. 7 Royal Oak, MI 48391</address>
    <ul class="contacts">
      <li><svg viewBox="0 0 20 20" aria-hidden="true"><path d="M10 1a9 9 0 1 0 0 18 9 9 0 0 0 0-18zm0 1.6a7.4 7.4 0 1 1 0 14.8 7.4 7.4 0 0 1 0-14.8z"/><path d="M7 5.5l1.6-.4 1 2.4-1 .9c.5 1.2 1.3 2 2.5 2.5l.9-1 2.4 1-.4 1.6c-3.4.2-7.3-3.7-7-7z"/></svg>(248) 555-0174</li>
      <li><svg viewBox="0 0 20 20" aria-hidden="true"><path d="M5 3h8l2 3H5zM2 7h16v8h-2v-3H4v3H2zM5 13h10v4H5z"/></svg>(248) 555-0189</li>
      <li><svg viewBox="0 0 20 20" aria-hidden="true"><path d="M2 8l8-5 8 5v9H2zm2 1.2l6 3.8 6-3.8L10 5.3z"/></svg>info@BrightwellDentalCareMi.com</li>
      <li class="web"><svg viewBox="0 0 20 20" aria-hidden="true"><path d="M10 1a9 9 0 1 0 0 18 9 9 0 0 0 0-18zm5.8 5h-2.7a13 13 0 0 0-1.2-3.2A7.5 7.5 0 0 1 15.8 6zM10 2.6c.7 1 1.2 2.1 1.5 3.4h-3c.3-1.3.8-2.4 1.5-3.4zM2.9 11.5a7.3 7.3 0 0 1 0-3h3a14 14 0 0 0 0 3zm1.3 2.5h2.7c.3 1.2.7 2.2 1.2 3.2A7.5 7.5 0 0 1 4.2 14zm2.7-8H4.2a7.5 7.5 0 0 1 3.9-3.2C7.6 3.8 7.2 4.8 6.9 6zM10 17.4c-.7-1-1.2-2.1-1.5-3.4h3c-.3 1.3-.8 2.4-1.5 3.4zm1.8-5.9H8.2a12 12 0 0 1 0-3h3.6a12 12 0 0 1 0 3zm.1 5.7c.5-1 .9-2 1.2-3.2h2.7a7.5 7.5 0 0 1-3.9 3.2zm2.2-5.7a14 14 0 0 0 0-3h3a7.3 7.3 0 0 1 0 3z"/></svg>BrigthwellDentalCareMi.com</li>
    </ul>
  </div>
</section>

<section class="card card--back" aria-label="Business card back, appointment reminder">
  <span class="watermark"></span>
  <h2 class="appt-title">YOUR APPOINTMENT</h2>

  <div class="field field--name">Name :<span class="fill" style="width:660px"></span></div>
  <div class="field field--date">Date :<span class="fill" style="width:186px;margin-left:26px"></span>Time :<span class="fill" style="width:240px"></span>am / pm</div>
  <div class="field field--next">Next Appointment<span class="slot" style="margin-left:24px"></span><span class="slot"></span><span class="slot"></span></div>

  <div class="days">
    <span>MON</span><i class="box"></i>
    <span>TUE</span><i class="box"></i>
    <span>WED</span><i class="box"></i>
    <span>THU</span><i class="box"></i>
    <span>FRI</span><i class="box"></i>
    <span>SAT</span><i class="box"></i>
  </div>

  <p class="notice">If you are unable to keep your appointment, kindly give 48 hours notice</p>
</section>

</body>
</html>
```